Garlic Farm for Farm Sales/Restaurant sales

Need a professional, but appealing to agriculture world. We are selling 27 kinds of Organic Garlic from a farm in Simla,CO. I have uploaded logo and business information-we are going to need a template, because I will need to use it for four separate people.
-We are trying to appeal to Farm to table restaurants
-As well as growers/farmers

Target Market(s)

Agriculture Sales/Restaurants-Organic

Industry/Entity Type

Agriculture

Contact Information for Business Card

Want it to look more unique then your average kelto stock card- I want it to look amazing

Font styles to use
Sans Serif

Colors
0455a3
ec1f27
fbed22
ffffff

Requirements
Must have
• Just be creative
Nice to have
• Colorful
Should not have
• plain

```html
<!DOCTYPE html>
<html lang="en">
<head>
<meta charset="utf-8">
<title>Plains Clove Gourmet Garlic – Business Card</title>
<link rel="stylesheet" href="https://fonts.googleapis.com/css2?family=Open+Sans:wght@400;600;700&display=swap">
<style>
  :root {
    --page-bg: #d9d5d0;
    --card-bg: #eceeef;
    --panel-red: #c51f2b;
    --panel-red-deep: #9e1420;
    --outline-navy: #1c1f3b;
    --accent-yellow: #f6b817;
    --text-white: #ffffff;
    --brand-navy: #1c1f3b;
    --tagline-red: #9e1420;
  }
  * { box-sizing: border-box; }
  html, body {
    margin: 0;
    width: 1200px;
    height: 969px;
    overflow: hidden;
    background: var(--page-bg);
    font-family: "Open Sans", Arial, sans-serif;
  }
  .business-card {
    position: absolute;
    left: 100px;
    top: 201px;
    width: 1000px;
    height: 567px;
    border-radius: 26px;
    background: var(--card-bg);
    overflow: hidden;
    box-shadow: 0 10px 30px rgba(0,0,0,0.18);
  }
  .red-panel {
    position: absolute;
    inset: 0;
  }
  .contact-block {
    position: absolute;
    left: 46px;
    top: 110px;
    color: var(--text-white);
  }
  .person-name {
    margin: 0;
    font-size: 33px;
    font-weight: 600;
    color: var(--accent-yellow);
    letter-spacing: 0.5px;
  }
  .person-title {
    margin: 4px 0 0;
    font-size: 22px;
    letter-spacing: 0.5px;
  }
  .postal-address {
    margin: 22px 0 0;
    font-style: normal;
    font-size: 23px;
    line-height: 39px;
  }
  .contact-list {
    list-style: none;
    margin: 10px 0 0;
    padding: 0;
    font-size: 23px;
    line-height: 38px;
  }
  .contact-list li {
    display: flex;
    align-items: center;
    gap: 12px;
  }
  .contact-list svg {
    width: 22px;
    height: 22px;
    flex: none;
  }
  .social-row {
    display: flex;
    gap: 8px;
    margin-top: 26px;
  }
  .social-dot {
    width: 34px;
    height: 34px;
    border-radius: 50%;
    border: 2px solid var(--accent-yellow);
  }
  .brand-block {
    position: absolute;
    left: 560px;
    top: 150px;
    width: 390px;
    text-align: center;
  }
  .brand-circle {
    width: 130px;
    height: 130px;
    border-radius: 50%;
    background: var(--panel-red);
    margin: 0 auto;
  }
  .brand-name {
    margin: 30px 0 0;
    font-size: 60px;
    font-weight: 700;
    color: var(--brand-navy);
    line-height: 1;
  }
  .brand-tagline {
    margin: 8px 0 0;
    font-size: 22px;
    font-weight: 600;
    color: var(--tagline-red);
    letter-spacing: 1px;
  }
</style>
</head>
<body>
  <section class="business-card">
    <svg class="red-panel" viewBox="0 0 1000 567" width="1000" height="567" role="img" aria-label="Red side panel with faint garlic bulb artwork">
      <defs>
        <linearGradient id="panelGradient" x1="0" y1="0" x2="1" y2="1">
          <stop offset="0" stop-color="var(--panel-red-deep)"/>
          <stop offset="0.5" stop-color="var(--panel-red)"/>
          <stop offset="1" stop-color="var(--panel-red-deep)"/>
        </linearGradient>
      </defs>
      <path d="M0 0 H430 C490 40 520 110 512 180 C506 230 470 262 420 268 C398 271 398 283 420 286 C470 293 496 340 490 400 C485 470 460 530 430 567 H0 Z" fill="url(#panelGradient)"/>
      <path d="M430 0 C490 40 520 110 512 180 C506 230 470 262 420 268 C398 271 398 283 420 286 C470 293 496 340 490 400 C485 470 460 530 430 567" fill="none" stroke="var(--outline-navy)" stroke-width="5"/>
    </svg>

    <div class="contact-block">
      <h1 class="person-name">DALE HARTWELL</h1>
      <p class="person-title">CEO/FOUNDER</p>
      <address class="postal-address">P.O. Box 48<br>Larkton, CO 80871</address>
      <ul class="contact-list">
        <li>
          <svg viewBox="0 0 24 24" aria-hidden="true"><path fill="var(--accent-yellow)" d="M6.6 10.8a15 15 0 0 0 6.6 6.6l2.2-2.2a1 1 0 0 1 1-.25 11.4 11.4 0 0 0 3.6.57 1 1 0 0 1 1 1V20a1 1 0 0 1-1 1A17 17 0 0 1 3 4a1 1 0 0 1 1-1h3.5a1 1 0 0 1 1 1c0 1.25.2 2.45.57 3.57a1 1 0 0 1-.25 1z"/></svg>
          555-014-2276
        </li>
        <li>
          <svg viewBox="0 0 24 24" aria-hidden="true"><path fill="var(--accent-yellow)" d="M3 5h18v14H3z"/><path fill="none" stroke="var(--panel-red)" stroke-width="1.6" d="M3 5l9 7 9-7"/></svg>
          mia@PlainsClove.com
        </li>
        <li>
          <svg viewBox="0 0 24 24" aria-hidden="true"><circle cx="12" cy="12" r="9" fill="var(--accent-yellow)"/><path fill="none" stroke="var(--panel-red)" stroke-width="1.4" d="M3 12h18M12 3c3 3 3 15 0 18M12 3c-3 3-3 15 0 18"/></svg>
          www.PlainsClove.com
        </li>
      </ul>
      <div class="social-row" aria-hidden="true">
        <span class="social-dot"></span>
        <span class="social-dot"></span>
        <span class="social-dot"></span>
        <span class="social-dot"></span>
      </div>
    </div>

    <div class="brand-block">
      <div class="brand-circle" aria-hidden="true"></div>
      <p class="brand-name">Plains Clove</p>
      <p class="brand-tagline">gourmet garlic</p>
    </div>
  </section>
</body>
</html>
```